Business card design Needed for new logo / Construction business, home extensions and new builds

We need a business card design using our new logo files which i will attach to this project :)

We are a small construction business specialising in home extensions, new builds and property development. We are very ambitious and would appreciate professional and elegant designs for our new business card.

Very serious about using the services on MakerQuarry and recently acquired our new logo from here :)

Please get involved, i will feedback when i can as i am very busy but can respond daily, thanks

Target Market(s)

People that want to build onto their houses, new building developments or adding too their existing property

Industry/Entity Type

Construction

Contact Information for Business Card

Renwick Tolliver Construction, Lionel Ashby (Managing Director), Tel 07822254961, email - info@renwick-tolliver, www.renwick-tolliver.co.uk

Colors

Designer to choose colors to be used in the design.

Requirements
Must have
• I like a deep grey on the back please. A lot of you have provided black from and back, try mixing things up a little. The black looks cool 😎 Thanks

```html
<!DOCTYPE html>
<html lang="en">
<head>
<meta charset="utf-8">
<title>Renwick Tolliver Construction – Business Card</title>
<link rel="stylesheet" href="https://fonts.googleapis.com/css2?family=Cinzel:wght@400;600&display=swap">
<style>
  :root {
    --backdrop: #b5b5b4;
    --card-black: #040404;
    --card-white: #ffffff;
    --deep-grey: #4b4b4b;
    --ink: #2b2526;
    --silver-text: #dcdde0;
    --gold: #d9a12c;
    --card-radius: 42px;
  }
  * { box-sizing: border-box; margin: 0; padding: 0; }
  html, body { width: 1200px; height: 850px; overflow: hidden; }
  body {
    background: var(--backdrop);
    font-family: "Cinzel", serif;
    position: relative;
  }
  .card {
    position: absolute;
    left: 321px;
    width: 553px;
    height: 330px;
    border-radius: var(--card-radius);
    overflow: hidden;
    box-shadow: 0 18px 22px rgba(0,0,0,0.28);
  }
  .card--front { top: 47px; background: var(--card-black); }
  .card--back { top: 419px; background: var(--card-white); }
  .card__texture { position: absolute; inset: 0; }
  .card--front .card__texture { background: var(--card-black); }
  .card--back .card__texture { background: var(--card-white); }
  .card__bands { position: absolute; inset: 0; width: 553px; height: 330px; }

  .brand {
    position: absolute;
    left: 150px;
    width: 350px;
    top: 120px;
    text-align: center;
    color: var(--silver-text);
    font-weight: 600;
  }
  .brand__mark {
    display: block;
    width: 18px;
    height: 18px;
    margin: 0 auto 30px;
    background: var(--gold);
  }
  .brand__name { font-size: 25px; letter-spacing: 0.5px; line-height: 1.05; }
  .brand__line { font-size: 17px; letter-spacing: 1px; line-height: 1.3; }

  .person { position: absolute; left: 64px; top: 40px; color: var(--ink); }
  .person__name { font-size: 27px; font-weight: 600; line-height: 1; letter-spacing: 0.3px; }
  .person__role { font-size: 17px; font-weight: 400; line-height: 1.2; margin-top: 2px; letter-spacing: 0.6px; }

  .contact { position: absolute; left: 65px; top: 144px; list-style: none; color: var(--ink); }
  .contact__item {
    display: flex;
    align-items: center;
    height: 22px;
    font-size: 16px;
    letter-spacing: 0.6px;
  }
  .contact__item + .contact__item { margin-top: 15px; }
  .contact__item:nth-child(3) { margin-top: 12px; }
  .contact__item:nth-child(4) { margin-top: 17px; }
  .contact__icon { width: 22px; height: 22px; margin-right: 12px; flex: none; }
</style>
</head>
<body>

<section class="card card--front" aria-label="Card front">
  <div class="card__texture" role="img" aria-label="Faint tiled brand-mark pattern on black"></div>
  <svg class="card__bands" viewBox="0 0 553 330" aria-hidden="true">
    <defs>
      <linearGradient id="gold-front" x1="0" y1="0" x2="0.35" y2="1">
        <stop offset="0" stop-color="#c0841a"/>
        <stop offset="0.4" stop-color="#fdd98b"/>
        <stop offset="0.72" stop-color="#c48a1f"/>
        <stop offset="1" stop-color="#f7b733"/>
      </linearGradient>
      <linearGradient id="silver-front" x1="0" y1="0" x2="0.2" y2="1">
        <stop offset="0" stop-color="#eceded"/>
        <stop offset="0.5" stop-color="#8e9299"/>
        <stop offset="1" stop-color="#e7e8ea"/>
      </linearGradient>
    </defs>
    <polygon points="0,0 130,0 52,113 0,37" fill="var(--deep-grey)"/>
    <polygon points="0,37 184,307 46,307 0,239" fill="url(#gold-front)"/>
    <polygon points="0,239 46,307 120,307 135,330 0,330" fill="url(#silver-front)"/>
  </svg>
  <div class="brand">
    <span class="brand__mark"></span>
    <p class="brand__name">RENWICK TOLLIVER</p>
    <p class="brand__line">CONSTRUCTION</p>
  </div>
</section>

<section class="card card--back" aria-label="Card back">
  <div class="card__texture" role="img" aria-label="Faint tiled brand-mark pattern on white"></div>
  <svg class="card__bands" viewBox="0 0 553 330" aria-hidden="true">
    <defs>
      <linearGradient id="gold-back" x1="1" y1="0" x2="0.65" y2="1">
        <stop offset="0" stop-color="#c0841a"/>
        <stop offset="0.4" stop-color="#fdd98b"/>
        <stop offset="0.72" stop-color="#c48a1f"/>
        <stop offset="1" stop-color="#f7b733"/>
      </linearGradient>
      <linearGradient id="silver-back" x1="1" y1="0" x2="0.8" y2="1">
        <stop offset="0" stop-color="#eceded"/>
        <stop offset="0.5" stop-color="#8e9299"/>
        <stop offset="1" stop-color="#e7e8ea"/>
      </linearGradient>
    </defs>
    <polygon points="422,0 553,0 553,37 500,113" fill="var(--card-black)"/>
    <polygon points="553,37 553,236 508,307 370,307" fill="url(#gold-back)"/>
    <polygon points="553,236 553,330 419,330 430,307 508,307" fill="url(#silver-back)"/>
  </svg>

  <div class="person">
    <h1 class="person__name">YOUR NAMER</h1>
    <p class="person__role">Founder</p>
  </div>

  <ul class="contact">
    <li class="contact__item">
      <svg class="contact__icon" viewBox="0 0 22 22" aria-hidden="true">
        <circle cx="11" cy="11" r="11" fill="var(--ink)"/>
        <path d="M11 5.2a3.6 3.6 0 0 0-3.6 3.6c0 2.7 3.6 7 3.6 7s3.6-4.3 3.6-7A3.6 3.6 0 0 0 11 5.2z" fill="#fff"/>
        <circle cx="11" cy="8.8" r="1.4" fill="var(--ink)"/>
      </svg>
      Your Adress
    </li>
    <li class="contact__item">
      <svg class="contact__icon" viewBox="0 0 22 22" aria-hidden="true">
        <circle cx="11" cy="11" r="11" fill="var(--ink)"/>
        <rect x="5.5" y="7.5" width="11" height="7.5" fill="none" stroke="#fff" stroke-width="1.1"/>
        <path d="M5.5 7.5 11 12l5.5-4.5M5.5 15l4-3.6M16.5 15l-4-3.6" fill="none" stroke="#fff" stroke-width="1"/>
      </svg>
      Your email
    </li>
    <li class="contact__item">
      <svg class="contact__icon" viewBox="0 0 22 22" aria-hidden="true">
        <circle cx="11" cy="11" r="11" fill="var(--ink)"/>
        <g fill="none" stroke="#fff" stroke-width="1">
          <circle cx="11" cy="11" r="5.8"/>
          <ellipse cx="11" cy="11" rx="2.6" ry="5.8"/>
          <path d="M5.2 11h11.6M6 8h10M6 14h10M11 5.2v11.6"/>
        </g>
      </svg>
      Your website
    </li>
    <li class="contact__item">
      <svg class="contact__icon" viewBox="0 0 22 22" aria-hidden="true">
        <circle cx="11" cy="11" r="11" fill="var(--ink)"/>
        <path d="M7.6 5.6l1.8-.4 1.2 2.9-1.3 1c.6 1.4 1.6 2.5 3 3.2l1-1.3 2.9 1.2-.4 1.8c-.2.6-.8 1-1.4.9-4-.5-7.2-3.7-7.7-7.7-.1-.6.3-1.2.9-1.6z" fill="#fff"/>
      </svg>
      Your number telephone
    </li>
  </ul>
</section>

</body>
</html>
```